Dynamic Business Card for Sports Supplements Company

Hi! I'm looking for an awesome business card to match my existing sports supplement company. I have uploaded my current company logo and screenshot of the front page of my website.

I would like to have something dynamic and interesting and utilize the colors in the website - the reds and purples

The business card should be double sided and focus on a unique eye-catching design on the back and include all the relevant company info.

Most importantly, it should say somewhere: "Sign up on our website for a coupon code."

Target Market(s)

Mostly for women gym goers but it shouldn't be too feminine. It should be in keeping with the website design. It should flow and clearly be connected to it

Industry/Entity Type

Business

Contact Information for Business Card

Lorraine K. Vestal
CEO
LVestal@Quorvanexco.com
www.quorvanexco.com
555.417.3820
P.O. Box 47315
Harlow, Oregon 00000

Sign up on our website for a coupon code

Font styles to use
Serif
Sans Serif
Other font styles liked:
• Novecento font family and "Quorvanex" is in AR Destine font

Requirements
Must have
• One side should be a bold Quorvanex logo design. Even just the symbol itself may be o.k. (see attached file)

```html
<!DOCTYPE html>
<html lang="en">
<head>
<meta charset="utf-8">
<title>Quorvanex Business Card</title>
<link href="https://fonts.googleapis.com/css2?family=Figtree:wght@400;500;800&display=swap" rel="stylesheet">
<style>
  :root {
    --backdrop: #3a3a3a;
    --card-black: #000000;
    --card-white: #ffffff;
    --brand-red: #e0202a;
    --ink: #111111;
    --ink-soft: #6b6b6b;
  }
  * { margin: 0; padding: 0; box-sizing: border-box; }
  html, body { width: 1200px; height: 855px; overflow: hidden; }
  body {
    background: var(--backdrop);
    font-family: "Figtree", "Helvetica Neue", Arial, sans-serif;
    position: relative;
  }
  .card {
    position: absolute;
    left: 354px;
    width: 492px;
    height: 280px;
    overflow: hidden;
    box-shadow: 0 4px 14px rgba(0,0,0,0.45);
  }
  /* Back side */
  .card-back { top: 137px; background: var(--card-black); }
  .back-mark {
    position: absolute;
    left: 188px; top: 82px;
    width: 116px; height: 116px;
    border: 7px solid var(--card-white);
    border-radius: 50%;
    display: flex; align-items: center; justify-content: center;
  }
  .back-mark-name {
    color: var(--card-white);
    font-weight: 800;
    font-size: 12px;
    letter-spacing: 0.4px;
  }
  .coupon-note {
    position: absolute;
    left: 0; right: 0; top: 240px;
    text-align: center;
    color: var(--card-white);
    font-size: 13px;
    font-weight: 400;
  }
  /* Front side */
  .card-front { top: 430px; height: 288px; background: var(--card-white); }
  .edge-band { position: absolute; left: 0; top: 0; width: 10px; height: 100%; }
  .contact {
    position: absolute; left: 26px; top: 0; color: var(--ink-soft);
    font-size: 13px; line-height: 16.5px;
  }
  .person-name {
    position: absolute; top: 118px; white-space: nowrap;
    font-size: 18px; font-weight: 500; color: var(--ink);
  }
  .person-title { position: absolute; top: 141px; }
  .address { position: absolute; top: 169px; white-space: nowrap; }
  .channels { position: absolute; top: 215px; list-style: none; white-space: nowrap; }
  .channels li { display: flex; align-items: center; gap: 6px; height: 16.5px; }
  .channels svg { width: 11px; height: 11px; flex: none; }
  .brand {
    position: absolute; left: 298px; top: 28px; width: 172px;
    text-align: center;
  }
  .brand-square {
    width: 60px; height: 60px; margin: 0 auto 18px;
    background: var(--brand-red);
  }
  .brand-name {
    font-weight: 800; font-size: 24px; line-height: 24px;
    color: var(--ink); letter-spacing: 1px;
  }
  .brand-tagline {
    font-size: 9.5px; color: var(--ink); letter-spacing: 0.5px; margin-top: 2px;
    white-space: nowrap;
  }
</style>
</head>
<body>

<section class="card card-back">
  <div class="back-mark"><span class="back-mark-name">QUORVANEX</span></div>
  <p class="coupon-note">Sign up on our website for a coupon code</p>
</section>

<section class="card card-front">
  <svg class="edge-band" viewBox="0 0 10 288" preserveAspectRatio="none">
    <polygon points="0,0 10,0 10,130 0,118" fill="var(--brand-red)"/>
    <polygon points="0,118 10,130 10,288 0,288" fill="var(--card-black)"/>
  </svg>

  <div class="contact">
    <h1 class="person-name">Lorraine K. Vestal</h1>
    <p class="person-title">CEO</p>
    <p class="address">P.O. Box 47315<br>Harlow, Oregon 00000</p>
    <ul class="channels">
      <li>
        <svg viewBox="0 0 12 12"><path d="M2.5 1 L4.5 1 L5 3.5 L3.8 4.3 C4.5 5.8 6 7.4 7.6 8.2 L8.5 7 L11 7.5 L11 9.5 C11 10.4 10.3 11 9.4 11 C5 10.6 1.4 7 1 2.6 C1 1.7 1.6 1 2.5 1 Z" fill="var(--brand-red)"/></svg>
        555.417.3820
      </li>
      <li>
        <svg viewBox="0 0 12 12"><rect x="0.5" y="2.5" width="11" height="7.5" fill="var(--brand-red)"/><path d="M0.5 2.5 L6 7 L11.5 2.5" stroke="var(--card-white)" stroke-width="1" fill="none"/></svg>
        LVestal@Quorvanexco.com
      </li>
      <li>
        <svg viewBox="0 0 12 12" fill="none" stroke="var(--brand-red)" stroke-width="1.1"><circle cx="6" cy="6" r="5"/><ellipse cx="6" cy="6" rx="2.2" ry="5"/><line x1="1" y1="6" x2="11" y2="6"/></svg>
        www.quorvanexco.com
      </li>
    </ul>
  </div>

  <div class="brand">
    <div class="brand-square"></div>
    <div class="brand-name">QUORVANEX</div>
    <div class="brand-tagline">STRONGER WITH EVERY REP</div>
  </div>
</section>

</body>
</html>
```